Business Card Design

We are a residential half way house for the addict ,the alcoholic and dual diagnosed in recovery.
i house both men and woman age 18+

Industry/Entity Type

Residential

```html
<!DOCTYPE html>
<html lang="en">
<head>
<meta charset="utf-8">
<title>Business Card – Willow Haven Sober Living Residence</title>
<link href="https://fonts.googleapis.com/css2?family=Lora:wght@400;500&display=swap" rel="stylesheet">
<style>
  :root {
    --bg: #e4e2de;
    --card-top: #ffffff;
    --card-bottom: #e9e9ea;
    --slate: #6b7283;
    --slate-band: #666d7b;
    --ink: #111111;
    --band: #161616;
    --text: #1c1c1c;
    --on-dark: #e8e8e8;
    --icon-bg: #2a2a2a;
    --icon-fg: #dddddd;
  }
  * { margin: 0; padding: 0; box-sizing: border-box; }
  html, body { width: 1200px; height: 892px; overflow: hidden; }
  body {
    background: var(--bg);
    font-family: "Lora", Georgia, serif;
    position: relative;
  }
  .card {
    position: absolute;
    left: 100px; top: 160px;
    width: 1000px; height: 572px;
    background: linear-gradient(180deg, var(--card-top) 0%, var(--card-bottom) 100%);
    overflow: hidden;
    box-shadow: 0 6px 18px rgba(0,0,0,0.18);
  }
  .card__base { position: absolute; left: 0; top: 0; width: 1000px; height: 572px; }

  .rule { position: absolute; height: 8px; }
  .rule--slate { left: 0; top: 292px; width: 560px; background: var(--slate); }
  .rule--black { left: 560px; top: 276px; width: 440px; background: var(--ink); }

  .brand { position: absolute; left: 60px; top: 150px; color: var(--slate); font-weight: 500; }
  .brand__name { font-size: 58px; line-height: 1.05; }
  .brand__tag { font-size: 30px; line-height: 1.25; margin-left: 40px; }

  .person { position: absolute; right: 40px; top: 196px; text-align: right; color: var(--text); }
  .person__name { font-size: 40px; line-height: 1; }
  .person__role { font-size: 19px; line-height: 1.3; }
  .person__note { position: absolute; right: 40px; top: 292px; font-size: 20px; line-height: 1.2; color: var(--text); }

  .contacts { position: absolute; list-style: none; font-size: 24px; color: var(--text); }
  .contacts li { display: flex; align-items: center; gap: 14px; height: 36px; }
  .contacts--office { left: 60px; top: 350px; }
  .contacts--direct { left: 570px; top: 320px; }
  .icon {
    width: 26px; height: 26px; flex: none;
    background: var(--icon-bg); border-radius: 3px;
    display: flex; align-items: center; justify-content: center;
  }
  .icon svg { width: 18px; height: 18px; }

  .address {
    position: absolute; left: 40px; top: 478px;
    display: flex; align-items: center; gap: 18px;
    color: var(--on-dark); font-size: 26px;
  }
  .address svg { width: 18px; height: 24px; }
</style>
</head>
<body>
  <div class="card">
    <svg class="card__base" viewBox="0 0 1000 572" aria-hidden="true">
      <path d="M830 420 L1000 420 L1000 572 L0 572 L0 540 L830 540 Z" fill="var(--slate-band)"/>
      <path d="M0 455 L700 455 L730 430 L800 430 Q830 430 840 455 L860 540 L0 540 Z" fill="var(--band)"/>
    </svg>

    <div class="rule rule--slate"></div>
    <div class="rule rule--black"></div>

    <div class="brand">
      <div class="brand__name">Willow Haven</div>
      <div class="brand__tag">Sober Living Residence</div>
    </div>

    <div class="person">
      <div class="person__name">Renee Castillo</div>
      <div class="person__role">Owner</div>
    </div>
    <div class="person__note">(House Manager)</div>

    <ul class="contacts contacts--office">
      <li><span class="icon"><svg viewBox="0 0 24 24"><path fill="var(--icon-fg)" d="M6.6 10.8a15 15 0 0 0 6.6 6.6l2.2-2.2c.3-.3.7-.4 1-.2 1.1.4 2.3.6 3.6.6.6 0 1 .4 1 1V20c0 .6-.4 1-1 1A17 17 0 0 1 3 4c0-.6.4-1 1-1h3.5c.6 0 1 .4 1 1 0 1.3.2 2.5.6 3.6.1.3 0 .7-.2 1z"/></svg></span>(555) 310-0142</li>
      <li><span class="icon"><svg viewBox="0 0 24 24"><path fill="var(--icon-fg)" d="M6.6 10.8a15 15 0 0 0 6.6 6.6l2.2-2.2c.3-.3.7-.4 1-.2 1.1.4 2.3.6 3.6.6.6 0 1 .4 1 1V20c0 .6-.4 1-1 1A17 17 0 0 1 3 4c0-.6.4-1 1-1h3.5c.6 0 1 .4 1 1 0 1.3.2 2.5.6 3.6.1.3 0 .7-.2 1z"/></svg></span>(555) 310-0143</li>
    </ul>

    <ul class="contacts contacts--direct">
      <li><span class="icon"><svg viewBox="0 0 24 24"><rect x="6" y="2" width="12" height="20" rx="2" fill="var(--icon-fg)"/><rect x="8" y="5" width="8" height="11" fill="var(--icon-bg)"/></svg></span>(555) 827-4410</li>
      <li><span class="icon"><svg viewBox="0 0 24 24"><rect x="3" y="6" width="18" height="12" fill="none" stroke="var(--icon-fg)" stroke-width="2"/><path d="M3 6 L12 13 L21 6" fill="none" stroke="var(--icon-fg)" stroke-width="2"/></svg></span>reneecastillo@example.com</li>
    </ul>

    <div class="address">
      <svg viewBox="0 0 18 24" aria-hidden="true"><path fill="var(--on-dark)" d="M9 0a9 9 0 0 0-9 9c0 6.5 9 15 9 15s9-8.5 9-15a9 9 0 0 0-9-9zm0 12.5A3.5 3.5 0 1 1 9 5.5a3.5 3.5 0 0 1 0 7z"/></svg>
      <span>2718 Palm Grove Rd. Bayview,Fla 33400</span>
    </div>
  </div>
</body>
</html>
```